Business card design Needed for new logo / Construction business, home extensions and new builds

We need a business card design using our new logo files which i will attach to this project :)

We are a small construction business specialising in home extensions, new builds and property development. We are very ambitious and would appreciate professional and elegant designs for our new business card.

Very serious about using the services on MakerQuarry and recently acquired our new logo from here :)

Please get involved, i will feedback when i can as i am very busy but can respond daily, thanks

Target Market(s)

People that want to build onto their houses, new building developments or adding too their existing property

Industry/Entity Type

Construction

Contact Information for Business Card

Renwick Tolliver Construction, Lionel Ashby (Managing Director), Tel 07822254961, email - info@renwick-tolliver, www.renwick-tolliver.co.uk

Colors

Designer to choose colors to be used in the design.

Requirements
Must have
• I like a deep grey on the back please. A lot of you have provided black from and back, try mixing things up a little. The black looks cool 😎 Thanks

```html
<!DOCTYPE html>
<html lang="en">
<head>
<meta charset="utf-8">
<title>Renwick Tolliver Construction – Business Card</title>
<link rel="stylesheet" href="https://fonts.googleapis.com/css2?family=Cinzel:wght@400;600&family=Open+Sans:wght@400;600;700&display=swap">
<style>
  :root {
    --page: #1c1c1f;
    --card-back: #2b2b2f;
    --card-front: #222226;
    --pattern-dark: #1f1f22;
    --pattern-light: #4a4a50;
    --gold: #d9a12a;
    --gold-light: #f0c453;
    --silver: #d6d6d8;
    --white: #f2f2f2;
    --emboss: #1a1a1d;
  }
  * { box-sizing: border-box; margin: 0; padding: 0; }
  html, body { width: 1200px; height: 780px; overflow: hidden; background: var(--page); }
  .canvas {
    width: 1200px; height: 780px;
    display: flex; align-items: center; justify-content: center; gap: 48px;
    font-family: "Open Sans", Arial, sans-serif;
  }
  .card {
    position: relative;
    width: 540px; height: 309px;
    border-radius: 4px;
    overflow: hidden;
    box-shadow: 0 18px 40px rgba(0,0,0,.55);
  }

  /* Back */
  .card-back { background: var(--card-back); }
  .back-pattern {
    position: absolute; inset: 0;
    background: linear-gradient(160deg, var(--pattern-light) 0%, var(--pattern-dark) 55%, var(--card-back) 100%);
  }
  .back-signature {
    position: absolute; right: 22px; top: 22px;
    display: flex; align-items: center; gap: 6px;
    font-family: "Cinzel", Georgia, serif; font-weight: 400;
    font-size: 9px; letter-spacing: .06em; color: var(--gold);
  }
  .back-signature .dot { width: 7px; height: 7px; background: var(--gold); }

  /* Front */
  .card-front { background: var(--card-front); }
  .accent-bar {
    position: absolute; right: 0; top: 20px;
    width: 10px; height: 56px;
    background: linear-gradient(180deg, var(--gold-light), var(--gold));
  }
  .holder {
    position: absolute; right: 28px; top: 22px; text-align: right;
  }
  .holder-name { font-size: 26px; font-weight: 700; line-height: 1.1; letter-spacing: .01em; }
  .holder-name .first { color: var(--silver); }
  .holder-name .last { color: var(--gold); }
  .holder-title { font-size: 13px; font-weight: 600; color: var(--white); margin-top: 2px; }

  .emboss-mark {
    position: absolute; right: 38px; top: 110px;
    width: 170px; height: 150px; border-radius: 6px;
    background: linear-gradient(145deg, #2a2a2e 0%, var(--emboss) 100%);
    box-shadow: inset 2px 2px 3px rgba(255,255,255,.05), inset -3px -3px 6px rgba(0,0,0,.45);
  }

  .brand {
    position: absolute; left: 30px; top: 104px;
    display: flex; align-items: center; gap: 10px;
  }
  .brand-square { width: 14px; height: 14px; background: var(--gold); }
  .brand-name {
    font-family: "Cinzel", Georgia, serif; font-weight: 600;
    font-size: 15px; line-height: 1.25; letter-spacing: .05em; color: var(--gold);
  }

  .contact {
    position: absolute; left: 30px; top: 178px;
    color: var(--white); font-size: 12.5px; line-height: 1.4;
  }
  .address { margin-bottom: 10px; }
  .contact-line { display: flex; align-items: center; gap: 8px; }
  .contact-line svg { width: 12px; height: 12px; flex: none; }
</style>
</head>
<body>
<main class="canvas">

  <section class="card card-back" aria-label="Card back">
    <div class="back-pattern" role="img" aria-label="Repeating brand monogram pattern in dark grey tones"></div>
    <div class="back-signature">
      <span class="dot"></span>
      <span>RENWICK TOLLIVER CONSTRUCTION</span>
    </div>
  </section>

  <section class="card card-front" aria-label="Card front">
    <div class="accent-bar"></div>
    <div class="holder">
      <p class="holder-name"><span class="first">Lionel</span> <span class="last">Ashby</span></p>
      <p class="holder-title">Managing Director</p>
    </div>

    <div class="emboss-mark" role="img" aria-label="Large embossed brand mark in black gloss"></div>

    <div class="brand">
      <span class="brand-square"></span>
      <p class="brand-name">RENWICK TOLLIVER<br>CONSTRUCTION</p>
    </div>

    <div class="contact">
      <p class="address">Calloway Road, Westbrook<br>Harlingford, HX4 7QT</p>
      <p class="contact-line">
        <svg viewBox="0 0 24 24" aria-hidden="true"><path fill="#d9a12a" d="M6.6 10.8a15.1 15.1 0 0 0 6.6 6.6l2.2-2.2a1 1 0 0 1 1-.25 11.4 11.4 0 0 0 3.6.57 1 1 0 0 1 1 1V20a1 1 0 0 1-1 1A17 17 0 0 1 3 4a1 1 0 0 1 1-1h3.5a1 1 0 0 1 1 1c0 1.25.2 2.45.57 3.57a1 1 0 0 1-.25 1z"/></svg>
        0782 225 4961
      </p>
      <p class="contact-line">
        <svg viewBox="0 0 24 24" aria-hidden="true"><rect x="2" y="5" width="20" height="14" rx="2" fill="#d9a12a"/><path d="M3 6l9 7 9-7" fill="none" stroke="#222226" stroke-width="1.6"/></svg>
        info@renwick-tolliver.co.uk
      </p>
      <p class="contact-line">
        <svg viewBox="0 0 24 24" aria-hidden="true"><circle cx="12" cy="12" r="10" fill="none" stroke="#d9a12a" stroke-width="2"/><path d="M2 12h20M12 2c3 3 3 17 0 20M12 2c-3 3-3 17 0 20" fill="none" stroke="#d9a12a" stroke-width="1.6"/></svg>
        www.renwick-tolliver.co.uk
      </p>
    </div>
  </section>

</main>
</body>
</html>
```